Business Card Design for Training Business

Clear Path Coaching is a new business that delivers training and other services with a focus on topics related to mental health and wellbeing, for example, Wellmind Response Course, Resilience etc. We have a strong focus on evidence-based psychology and neuroscience. I have a logo which I will upload with the brief, so please consider colours that work well with the logo.
Target Market(s)
Adults, workplaces (particularly government and not-for-profits)
Industry/Entity Type
Business
Contact Information for Business Card
Head Strong TrainingSamantha SellwoodDirector0438 770 850sam@headstrongtraining.com.auwww.headstrongtraining.com.au

```html
<!DOCTYPE html>
<html lang="en">
<head>
<meta charset="utf-8">
<title>Clear Path Coaching – Business Card</title>
<link rel="stylesheet" href="https://fonts.googleapis.com/css2?family=Arimo:wght@400;700&family=Open+Sans:wght@600&display=swap">
<style>
  :root {
    --backdrop: #d8d5cf;
    --card-black: #060606;
    --teal: #2aa3a7;
    --paper-light: #ffffff;
    --paper-shade: #e6e6e6;
    --ink: #111111;
    --brand-grey: #3a3a3a;
  }
  * { margin: 0; padding: 0; box-sizing: border-box; }
  html, body {
    width: 1200px;
    height: 892px;
    overflow: hidden;
    background: var(--backdrop);
  }
  .canvas {
    position: relative;
    width: 1200px;
    height: 892px;
    display: flex;
    align-items: center;
    justify-content: center;
  }
  .business-card {
    position: relative;
    width: 900px;
    height: 514px;
    border-radius: 34px;
    overflow: hidden;
    background: linear-gradient(160deg, var(--paper-light) 30%, var(--paper-shade) 100%);
    box-shadow: 0 18px 40px rgba(0,0,0,0.25);
  }
  .card-shapes {
    position: absolute;
    inset: 0;
    width: 100%;
    height: 100%;
  }
  .brand {
    position: absolute;
    left: 0;
    top: 0;
    width: 400px;
    height: 514px;
    display: flex;
    flex-direction: column;
    align-items: center;
    justify-content: center;
    gap: 34px;
  }
  .brand-dot {
    width: 150px;
    height: 150px;
    border-radius: 50%;
    border: 2px solid var(--teal);
  }
  .brand-name {
    font-family: "Arimo", sans-serif;
    font-weight: 400;
    font-size: 30px;
    letter-spacing: 4px;
    text-transform: uppercase;
    color: var(--brand-grey);
    text-align: center;
    line-height: 1.3;
  }
  .contact {
    position: absolute;
    left: 480px;
    right: 20px;
    top: 112px;
    text-align: center;
    color: var(--ink);
  }
  .contact-name {
    font-family: "Open Sans", sans-serif;
    font-weight: 600;
    font-size: 42px;
    line-height: 1.1;
  }
  .contact-role {
    font-family: "Arimo", sans-serif;
    font-weight: 700;
    font-size: 25px;
    margin-top: 8px;
  }
  .contact-details {
    font-family: "Arimo", sans-serif;
    font-weight: 400;
    font-size: 23px;
    line-height: 1.3;
    margin-top: 30px;
    list-style: none;
  }
</style>
</head>
<body>
<main class="canvas">
  <section class="business-card">
    <svg class="card-shapes" viewBox="0 0 900 514" preserveAspectRatio="none" aria-hidden="true">
      <path d="M0 0 H352 Q490 257 370 514 H0 Z" fill="var(--teal)" transform="translate(9 0)"/>
      <path d="M0 0 H352 Q490 257 370 514 H0 Z" fill="var(--card-black)"/>
    </svg>

    <div class="brand">
      <div class="brand-dot"></div>
      <p class="brand-name">Clear Path<br>Coaching</p>
    </div>

    <div class="contact">
      <h1 class="contact-name">Rebecca Tanfield</h1>
      <p class="contact-role">Director</p>
      <ul class="contact-details">
        <li>0491 362 517</li>
        <li>bec@clearpathcoaching.example.au</li>
        <li>www.clearpathcoaching.example.au</li>
      </ul>
    </div>
  </section>
</main>
</body>
</html>
```